We need a flyer design that can be mailed using envelope stuffing services like Coin Courier. Ridgeway Frost Depot owns and operates ice vending machines. These machines make, bag and sell the ice much like a soda or snack vending machine but of course are much larger.
The machines sell a 16lb bag of ice for $2. They will accept bills,coin, credit cards and do provide change. They bag the ice automatically on demand so it is never frozen together. The machines are super convenient as you can drive up to them and put the bag directly into the trunk of your car or the bed of your truck. See ridgefrostco.example
The flyer does need to be in 2 languages.
We have 5 locations that we want people to know about
The five addresses are:
4720 W Larkin St., Plano, TX 75074
2615 R Ave, Plano, TX 75074
1470 W Cedar Blvd, Plano, TX 75074
5100 Dunmore, Plano TX 75075
4830 FM 917, Wylie, TX 75098

The attached shows what we have done in the past but it is outdated and could do with better graphics.

Target Market(s)

Our target audience is local landscape businesses, roofers, construction crews, soccer moms, fishermen, boaters, hunters etc. It's a pretty broad audience since ice is so heavily used in the US, much more than any other part of the world. The target would demographic would be adults, blue collar families.

Industry/Entity Type

House

Requirements
Must have
• Must have an image. Must highlight the benefits of the ice vending machine:
Open 24 hours
Fully automatic
Sanitary - untouched by human hands
16 lbs for $2 is Double Chill Deal that you would get from a typical grocery store or gas station where the norm is 7-8 lb bags for the same price.
Double Chill Deal can be used though it is copyrighted by the manufacturer of the machines but as someone who has bought the machine we are granted the right to use it in promotional materials.

```html
<!DOCTYPE html>
<html lang="en">
<head>
<meta charset="utf-8">
<title>Need Ice? – Ridgeway Frost Depot</title>
<link rel="stylesheet" href="https://fonts.googleapis.com/css2?family=Roboto:wght@400;700;900&family=Roboto+Condensed:wght@400;700;900&display=swap">
<style>
  :root {
    --ice-blue: #1a6fb8;
    --ice-blue-dark: #0b4f8c;
    --band-top: #0d5c9e;
    --band-bottom: #0a4f8a;
    --gold: #b8891c;
    --gold-light: #e0b43a;
    --gold-dark: #8a6410;
    --ink: #222;
    --paper-top: #f4f4f4;
    --paper-bottom: #d9d9d9;
    --footer: #3a3a3a;
    --white: #fff;
  }
  * { box-sizing: border-box; margin: 0; padding: 0; }
  html, body { width: 786px; height: 1200px; overflow: hidden; }
  body { font-family: "Roboto", Arial, sans-serif; background: #fff; }

  .flyer { position: relative; width: 786px; height: 1200px; overflow: hidden; }

  .hero {
    position: absolute; left: 0; top: 0; width: 786px; height: 828px;
    background: linear-gradient(180deg, var(--paper-top) 0%, #ebebeb 50%, var(--paper-bottom) 100%);
  }
  .headline {
    position: absolute; left: 0; top: 40px; width: 786px; text-align: center;
    font-family: "Roboto", Arial, sans-serif; font-weight: 900; font-size: 150px;
    letter-spacing: -5px; line-height: 1;
    color: var(--ice-blue);
    text-shadow: 0 3px 0 var(--ice-blue-dark), 0 6px 10px rgba(0,0,0,.25);
  }
  .headline-es {
    position: absolute; left: 0; top: 200px; width: 786px; text-align: center;
    font-family: "Roboto Condensed", Arial, sans-serif; font-weight: 900; font-size: 34px;
    color: var(--ice-blue-dark); letter-spacing: 1px;
  }

  .deal {
    position: absolute; left: 30px; top: 262px; width: 340px;
    font-family: "Roboto Condensed", Arial, sans-serif; color: var(--ink);
  }
  .deal-title { font-weight: 900; font-size: 34px; color: var(--gold); line-height: 1.05; }
  .deal-title-es { font-weight: 700; font-size: 22px; color: var(--gold-dark); line-height: 1.2; }
  .deal-note { font-size: 16px; line-height: 1.3; margin-top: 6px; }
  .deal-note em { font-style: normal; color: var(--ice-blue-dark); }
  .pay { margin-top: 12px; font-weight: 700; font-size: 17px; color: var(--ice-blue-dark); line-height: 1.3; }
  .pay-es { font-weight: 400; font-size: 15px; color: var(--ink); line-height: 1.3; }

  .machine-photo {
    position: absolute; left: 385px; top: 258px; width: 395px; height: 570px;
    background:
      linear-gradient(180deg, #ece8c8 0%, #e6e0bc 18%, #2b67b5 18%, #1d4f99 30%, #e8e2c2 30%, #ddd6b4 86%, #5a4b47 86%, #3f3431 100%);
  }
  .ice-bag-photo {
    position: absolute; left: 38px; top: 495px; width: 124px; height: 315px;
    border-radius: 40px 40px 30px 30px;
    background: linear-gradient(180deg, #f5f8fb 0%, #dde8f2 50%, #c7d6e6 100%);
  }

  .price-badge { position: absolute; left: 140px; top: 530px; width: 265px; height: 285px; }
  .price-badge .disc-text {
    position: absolute; left: 0; width: 100%; text-align: center;
    font-family: "Roboto Condensed", Arial, sans-serif; font-weight: 900; line-height: 1;
  }
  .price-weight { top: 82px; font-size: 60px; color: var(--white); text-shadow: 0 3px 4px rgba(0,0,0,.45); letter-spacing: -1px; }
  .price-only { top: 140px; font-size: 38px; color: var(--gold-dark); padding-left: 60px; }
  .price-amount { top: 172px; font-size: 86px; font-weight: 400 !important; color: var(--ink); padding-left: 20px; }

  .benefits {
    position: absolute; left: 0; top: 828px; width: 786px; height: 305px;
    background: linear-gradient(180deg, var(--band-top), var(--band-bottom));
  }
  .benefit-card {
    position: absolute; top: 24px; width: 166px; height: 243px;
    background: var(--white); border-radius: 14px;
    text-align: center;
    font-family: "Roboto Condensed", Arial, sans-serif; font-weight: 900;
  }
  .benefit-card svg { position: absolute; left: 28px; top: 16px; }
  .benefit-title { position: absolute; left: 0; width: 100%; line-height: 1; }
  .benefit-es {
    position: absolute; top: 274px; width: 166px; text-align: center;
    font-family: "Roboto Condensed", Arial, sans-serif; font-weight: 700; font-size: 14px;
    color: var(--white); letter-spacing: .3px;
  }
  .card-open { left: 38px; }
  .card-price { left: 218px; }
  .card-safe { left: 398px; }
  .card-auto { left: 578px; }
  .blue { color: var(--ice-blue-dark); }
  .gold { color: var(--gold); }

  .locations {
    position: absolute; left: 0; top: 1133px; width: 786px; height: 67px;
    background: var(--footer); display: flex; align-items: center; padding-left: 14px;
  }
  .locations-label {
    font-family: "Roboto Condensed", Arial, sans-serif; font-weight: 700; font-size: 26px;
    color: var(--gold-light); margin-right: 12px; letter-spacing: -.5px; line-height: 1;
  }
  .locations-label small { display: block; font-size: 12px; letter-spacing: 1px; margin-top: 2px; }
  .address {
    color: #eee; font-family: "Roboto Condensed", Arial, sans-serif; font-size: 14px; line-height: 1.25;
    padding: 0 10px; border-left: 1px dotted #888; white-space: nowrap;
  }
  .locations-label + .address { border-left: none; padding-left: 0; }
</style>
</head>
<body>
<main class="flyer">
  <section class="hero">
    <h1 class="headline">NEED ICE ?</h1>
    <p class="headline-es" lang="es">¿NECESITA HIELO?</p>

    <div class="deal">
      <p class="deal-title">DOUBLE CHILL DEAL</p>
      <p class="deal-title-es" lang="es">¡El doble de hielo!</p>
      <p class="deal-note">16 lbs for $2 – stores sell 7–8 lbs for the same price.<br><em lang="es">16 lb por $2 – el doble que en la tienda.</em></p>
      <p class="pay">Bills · Coins · Cards · Change given</p>
      <p class="pay-es" lang="es">Billetes · Monedas · Tarjetas · Da cambio</p>
    </div>

    <div class="ice-bag-photo" role="img" aria-label="Photo of a 16 lb Ridgeway Frost Depot bag of ice"></div>
    <div class="machine-photo" role="img" aria-label="Photo of the drive-up ice vending kiosk with blue awning, ICE sign and two chutes"></div>

    <div class="price-badge">
      <svg width="265" height="285" viewBox="0 0 265 285">
        <defs>
          <radialGradient id="goldDisc" cx="40%" cy="35%" r="70%">
            <stop offset="0" stop-color="#f0c44a"/>
            <stop offset=".6" stop-color="#c8961f"/>
            <stop offset="1" stop-color="#9a6d10"/>
          </radialGradient>
          <path id="rimArc" d="M 12 152 A 121 121 0 0 1 254 152"/>
        </defs>
        <circle cx="133" cy="155" r="115" fill="url(#goldDisc)"/>
        <text font-family="Roboto, Arial, sans-serif" font-size="15" letter-spacing="2" fill="#222">
          <textPath href="#rimArc" startOffset="50%" text-anchor="middle">www.ridgefrostco.example</textPath>
        </text>
      </svg>
      <div class="disc-text price-weight">16LBS</div>
      <div class="disc-text price-only">ONLY</div>
      <div class="disc-text price-amount">$2</div>
    </div>
  </section>

  <section class="benefits">
    <div class="benefit-card card-open">
      <svg width="110" height="110" viewBox="0 0 110 110" aria-hidden="true">
        <circle cx="55" cy="55" r="47" fill="none" stroke="#0b4f8c" stroke-width="8"/>
        <g stroke="#0b4f8c" stroke-width="4">
          <line x1="55" y1="14" x2="55" y2="22"/><line x1="55" y1="88" x2="55" y2="96"/>
          <line x1="14" y1="55" x2="22" y2="55"/><line x1="88" y1="55" x2="96" y2="55"/>
        </g>
        <path d="M55 55 L34 38 M55 55 L84 55" stroke="#0b4f8c" stroke-width="6" stroke-linecap="round" fill="none"/>
        <circle cx="55" cy="55" r="5" fill="#0b4f8c"/>
      </svg>
      <div class="benefit-title blue" style="top:132px;font-size:58px">OPEN</div>
      <div class="benefit-title gold" style="top:190px;font-size:38px">24HOUR</div>
    </div>
    <p class="benefit-es" lang="es" style="left:38px">ABIERTO 24 HORAS</p>

    <div class="benefit-card card-price">
      <svg width="110" height="110" viewBox="0 0 110 110" aria-hidden="true">
        <path d="M40 8 L70 8 L62 26 L48 26 Z" fill="#0b4f8c"/>
        <path d="M46 28 C18 40 8 70 14 88 C20 104 90 104 96 88 C102 70 92 40 64 28 Z" fill="#0b4f8c"/>
        <text x="55" y="78" text-anchor="middle" font-family="Roboto Condensed, Arial, sans-serif" font-weight="700" font-size="17" fill="#fff">16LBS</text>
      </svg>
      <div class="benefit-title gold" style="top:132px;font-size:52px">16LBS</div>
      <div class="benefit-title blue" style="top:190px;font-size:30px">ONLY $2</div>
    </div>
    <p class="benefit-es" lang="es" style="left:218px">16 LB SOLO $2</p>

    <div class="benefit-card card-safe">
      <svg width="110" height="110" viewBox="0 0 110 110" aria-hidden="true">
        <circle cx="55" cy="55" r="47" fill="none" stroke="#0b4f8c" stroke-width="8"/>
        <path d="M47 28 H63 V47 H82 V63 H63 V82 H47 V63 H28 V47 H47 Z" fill="#0b4f8c"/>
      </svg>
      <div class="benefit-title gold" style="top:138px;font-size:46px">SAFE</div>
      <div class="benefit-title blue" style="top:182px;font-size:22px;font-weight:700">UNTOUCHED<br>BY HANDS</div>
    </div>
    <p class="benefit-es" lang="es" style="left:398px">SIN CONTACTO HUMANO</p>

    <div class="benefit-card card-auto">
      <svg width="110" height="110" viewBox="0 0 110 110" aria-hidden="true">
        <rect x="64" y="6" width="11" height="11" fill="#0b4f8c"/>
        <rect x="78" y="6" width="11" height="11" fill="#0b4f8c"/>
        <rect x="64" y="20" width="11" height="11" fill="#0b4f8c"/>
        <rect x="78" y="20" width="11" height="11" fill="#0b4f8c"/>
        <path d="M40 16 C40 8 54 8 54 16 V52 C58 46 68 48 68 54 C72 50 82 52 82 58 C86 56 96 58 96 66 V80 C96 96 84 104 70 104 H56 C46 104 38 98 32 88 L16 66 C12 58 20 52 28 58 L40 70 Z" fill="#1a6fb8"/>
      </svg>
      <div class="benefit-title blue" style="top:140px;font-size:44px">FULLY</div>
      <div class="benefit-title gold" style="top:182px;font-size:56px">AUTO</div>
    </div>
    <p class="benefit-es" lang="es" style="left:578px">TOTALMENTE AUTOMÁTICO</p>
  </section>

  <footer class="locations">
    <span class="locations-label">LOCATIONS<small lang="es">UBICACIONES</small></span>
    <span class="address">4720 W Larkin St.,<br>Plano, TX 75074</span>
    <span class="address">2615 R Ave,<br>Plano, TX 75074</span>
    <span class="address">1470 W Cedar Blvd,<br>Plano, TX 75074</span>
    <span class="address">5100 Dunmore,<br>Plano TX 75075</span>
    <span class="address">4830 FM 917,<br>Wylie, TX 75098</span>
  </footer>
</main>
</body>
</html>
```